Ridge Lass Crew (Flyer)

I want a flyer to advertise my service.
Details below, and logo's to use are attached.

A girls only after school program, 11-14yrs, as OSHC is no longer avail, dedicated to coaching & mentoring our girls into strong, independent young women.

The Brainchild of Rebecca Folwin, Ridge Lass Crew was created to address the growing demand for after school/school holiday supervision for kids moving from primary into high school, when OSHC ceases to exist.
With over 12 years experience mentoring and coaching young women in the corporate world, Bec decided to leave her role as a Director with Tarrant Trust, and follow her passion.
Bec, along with her sister Lorraine, who has over 10 years experience in local communities as a Youth Worker, and is also a qualified Enrolled Nurse, embarked on building a program designed to keep parents happy (by knowing their girls are safe) and dedicated to coaching and mentoring our girls into strong, independent young women.
Open every afternoon and during school holidays, we look to offer;
- Daily meditation
- Healthy snacks
- Dedicated homework time
- Organised group activity, led by qualified instructors (yoga, fitness class, soccer etc)
- Regular guests speakers, addressing issues/concerns for young people today
- SOCIAL MEDIA FREE ZONE

Located 87 Pelham Pde, Baulkham Hills (across from Crestmoor Day Clinic)
Open 3-6pm Monday to Friday

Facebook page: http://fb.example/ridgelasscrew
Email: info@ridgelasscrew.example.au
Mobile: 0455817396

Target Market(s)

Parents of teenage girls, teenage girls 11-14 years

Industry/Entity Type

School

Font styles to use
Sans Serif

Colors
b768aa
e667a6

Requirements
Must have
• What progam is - see brief
• Who runs it
Should not have
• Not be too busy, not overly mature images

```html
<!DOCTYPE html>
<html lang="en">
<head>
<meta charset="utf-8">
<title>Ridge Lass Crew – After School Program Flyer</title>
<link href="https://fonts.googleapis.com/css2?family=Lobster+Two:ital,wght@0,400;0,700;1,400&family=Righteous&family=Poiret+One&family=Open+Sans:wght@400;700&family=Kalam:wght@700&family=Roboto+Condensed&display=swap" rel="stylesheet">
<style>
  :root {
    --pink: #e667a6;
    --purple: #b768aa;
    --purple-deep: #6d3e74;
    --ink: #2b2030;
    --blush: #f8d3ea;
    --white: #ffffff;
    --bullet: #d8344f;
    --paper: #f1eff0;
    --paper-mid: #dedcde;
    --gold-soft: #eadfc8;
  }
  * { margin: 0; padding: 0; box-sizing: border-box; }
  html, body { width: 848px; height: 1200px; overflow: hidden; background: var(--white); }
  .flyer { position: relative; width: 848px; height: 1200px; overflow: hidden; font-family: "Open Sans", sans-serif; }
  .backdrop { position: absolute; inset: 0; }
  .photo-panel {
    position: absolute; left: 553px; top: 0; width: 295px; height: 1112px;
    background:
      radial-gradient(ellipse 180px 260px at 230px 560px, rgba(234, 223, 200, 0.85), rgba(234, 223, 200, 0) 70%),
      radial-gradient(ellipse 220px 300px at 150px 900px, rgba(255, 255, 255, 0.9), rgba(255, 255, 255, 0) 70%),
      linear-gradient(165deg, var(--paper) 0%, #e9e7ea 30%, var(--paper-mid) 55%, #c9c6ca 75%, var(--paper) 100%);
  }
  .brand {
    position: absolute; left: 46px; top: 138px; width: 220px;
    font-family: "Open Sans", sans-serif; font-weight: 700; font-size: 38px; line-height: 1.15;
    color: var(--pink); text-align: center;
  }
  .headline {
    position: absolute; left: 406px; top: 112px; width: 407px; height: 214px;
    background: rgba(183, 104, 170, 0.92); border-radius: 10px;
    color: var(--white); font-family: "Lobster Two", cursive; text-align: center;
    padding-top: 12px;
  }
  .headline .l1 { font-size: 56px; line-height: 66px; }
  .headline .l2 { font-size: 38px; line-height: 56px; font-weight: 700; }
  .headline .l3 { font-size: 58px; line-height: 68px; }
  .oshc-note {
    position: absolute; left: 526px; top: 323px;
    font-size: 16px; color: var(--ink); letter-spacing: 0.2px;
  }
  .founder {
    position: absolute; left: 96px; top: 374px; width: 668px; height: 246px;
    background: rgba(183, 104, 170, 0.92); text-align: center;
  }
  .founder h1 {
    font-family: "Righteous", sans-serif; font-weight: 400; font-size: 33px;
    color: var(--ink); margin-top: 30px; letter-spacing: 0.5px;
  }
  .founder h2 {
    font-family: "Poiret One", sans-serif; font-weight: 400; font-size: 31px;
    color: var(--ink); margin-top: 4px; letter-spacing: 1px;
  }
  .founder .mission {
    font-family: "Lobster Two", cursive; font-style: italic; font-size: 32px; line-height: 44px;
    color: var(--blush); margin-top: 14px;
  }
  .offer-title {
    position: absolute; left: 58px; top: 655px;
    font-weight: 700; font-size: 23px; color: var(--purple-deep); letter-spacing: 0.5px;
  }
  .offer-list { position: absolute; left: 30px; top: 716px; list-style: none; }
  .offer-list li {
    position: relative; padding-left: 32px;
    font-family: "Lobster Two", cursive; font-size: 26px; color: var(--ink); line-height: 28px;
    letter-spacing: 0.6px;
  }
  .offer-list li::before {
    content: ""; position: absolute; left: 2px; top: 10px;
    border-left: 7px solid var(--bullet); border-top: 5px solid transparent; border-bottom: 5px solid transparent;
  }
  .offer-list li + li { margin-top: 15px; }
  .offer-list li.multi { line-height: 34px; }
  .offer-list li.multi::before { top: 13px; }
  .hours {
    position: absolute; left: 126px; top: 1030px;
    font-family: "Kalam", cursive; font-weight: 700; font-size: 30px; color: var(--ink); white-space: nowrap;
  }
  .hours .times { display: block; font-size: 23px; margin-left: 142px; margin-top: -6px; }
  .contact-band {
    position: absolute; left: 0; top: 1122px; width: 553px; height: 78px;
    background: #c680bb; color: var(--white); font-family: "Roboto Condensed", sans-serif;
  }
  .address { position: absolute; left: 18px; top: 16px; display: flex; gap: 14px; }
  .address .street { font-size: 19px; }
  .address .landmark { font-size: 12px; display: block; margin-top: 2px; }
  .phone { position: absolute; left: 324px; top: 26px; display: flex; align-items: center; gap: 10px; font-size: 20px; }
  .online {
    position: absolute; right: 18px; top: 1118px; text-align: right;
    font-family: "Roboto Condensed", sans-serif; color: var(--ink); font-size: 16px; line-height: 27px;
  }
  .online .label { display: flex; justify-content: flex-end; align-items: center; gap: 6px; font-size: 18px; }
  .online .web { display: flex; justify-content: flex-end; align-items: center; gap: 8px; }
  .online .web::after { content: ""; width: 14px; height: 14px; background: var(--purple); border-radius: 2px; }
</style>
</head>
<body>
<div class="flyer">
  <svg class="backdrop" width="848" height="1200" viewBox="0 0 848 1200" aria-hidden="true">
    <polygon points="553,0 553,1200 0,1200 0,345 332,345 332,250 240,196" fill="var(--pink)"/>
  </svg>
  <div class="photo-panel" role="img" aria-label="Soft-focus photo of an open monthly planner with spiral binding"></div>

  <div class="brand">Ridge Lass Crew</div>

  <div class="headline">
    <div class="l1">A Girls Only</div>
    <div class="l2">After School Program</div>
    <div class="l3">For 11-14yrs</div>
  </div>
  <p class="oshc-note">as OSHC is no longer available</p>

  <section class="founder">
    <h1>THE BRAINCHILD OF REBECCA FOLWIN</h1>
    <h2>RIDGE LASS CREW</h2>
    <p class="mission">Dedicated to Coaching &amp; Mentoring Our Girls<br>into Strong, Independent Young women</p>
  </section>

  <h3 class="offer-title">WHAT WE OFFER</h3>
  <ul class="offer-list">
    <li>Daily meditation</li>
    <li>Healthy snacks</li>
    <li class="multi">Organised group activity,<br>&nbsp;(yoga, fitness class, soccer etc.)</li>
    <li>Regular guests speakers</li>
    <li>Dedicated homework time</li>
    <li>Social media free zone</li>
  </ul>

  <p class="hours">Open every afternoon &amp; during school holidays<span class="times">3-6pm Monday to Friday</span></p>

  <footer class="contact-band">
    <div class="address">
      <svg width="18" height="24" viewBox="0 0 18 24" aria-hidden="true"><path d="M9 1C4.6 1 1 4.4 1 8.8 1 14.6 9 23 9 23s8-8.4 8-14.2C17 4.4 13.4 1 9 1z" fill="none" stroke="#fff" stroke-width="1.5"/><circle cx="9" cy="9" r="3" fill="none" stroke="#fff" stroke-width="1.5"/></svg>
      <div><span class="street">87 Pelham Pde, Baulkham Hills</span><span class="landmark">(across from Crestmoor Day Clinic)</span></div>
    </div>
    <div class="phone">
      <svg width="24" height="24" viewBox="0 0 24 24" aria-hidden="true"><path d="M6 3l3 4-2 2c1 3 4 6 7 7l2-2 4 3-2 3C11 20 4 13 3 5z" fill="none" stroke="#fff" stroke-width="1.4"/></svg>
      <span>Call: 0455817396</span>
    </div>
  </footer>

  <div class="online">
    <div class="label">e-Mail us
      <svg width="20" height="16" viewBox="0 0 20 16" aria-hidden="true"><rect x="1" y="1" width="18" height="14" fill="none" stroke="#2b2030" stroke-width="1.3"/><path d="M1 1l9 8 9-8" fill="none" stroke="#2b2030" stroke-width="1.3"/></svg>
    </div>
    <div>info@ridgelasscrew.example.au</div>
    <div class="web">http://fb.example/ridgelasscrew</div>
  </div>
</div>
</body>
</html>
```